Chamber of Commerce Web formcraft Project

We are working with Harborlight Chamber of Commerce. They are a new chamber of commerce forming in SoCal.
Some sites to use for inspiration:
https://brevinmarchamber.org
https://quellford.org
https://www.dorwickhavenchamber.com
https://www.tpchamber.com
https://velmorintcc.org
Thank you for taking the time to consider designing a website for us. We are web developers based in Stockton, CA, USA. Most of our projects go through the same process. Understanding this process may help you win a project with us. We custom-code all of our websites in-house. We don’t have any requirements as to what tools you use for your formcraft, but we prefer Figma files. For any formcraft that we label as four-stars, we send it to the client for review. The client picks the final formcraft they want us to use. Once we complete this process, we will continue to show additional clients all the four-star sites and purchase them later. Your designs will have multiple chances to sell. For better chances of success, we ask that you follow these guidelines.
IMAGES:
If you use any images or icons in the formcraft, we ask that you have a link to the asset so we can purchase the image/icon. Most of the designs we submit do not have the customer’s images on them unless they have some great images. Be creative; show us the feeling you are trying to portray with your image choices. Use any royalty-free site you choose. We subscribe to Adobe and mainly use their images, but we can purchase images outside of Adobe.
PLEASE NOTE: we will not submit designs to clients with watermarks on the images.
FONTS:
We ask that you identify the fonts used in the formcraft. This can be done in a message if you want. We typically use Google Fonts and Adobe Fonts.
CONTENT:
We're always open to different content and ideas. We often submit designs with stock images so the client can see our vision. We typically take pictures after the website launch to use their images with our vision. Lorem Ipsum is fine for paragraphs, but we ask that you write the headers in correct English. We want to be able to show the vision and identify the sections of the website.
INSPIRATION:
We typically add a couple of links in the brief of websites we like to help you get started in your formcraft.
REVISIONS:
We do not often ask for revisions of the designs unless we see something in the formcraft that may not appeal to the client. If there are slight changes that we want to make, we do that in the development process.
FEEDBACK:
We rarely give feedback on designs during the formcraft process. We are working on many website projects and do not have the time to provide feedback. We usually respond if your request is well thought out and asks specific questions, but a note asking “feedback, please” usually goes unanswered.

```html
<!DOCTYPE html>
<html lang="en">
<head>
<meta charset="utf-8">
<title>Harborlight Chamber of Commerce</title>
<link href="https://fonts.googleapis.com/css2?family=Roboto+Condensed:wght@500;700&family=Roboto:wght@400;500;700&display=swap" rel="stylesheet">
<style>
:root{
  --blue:#1a82f7;
  --blue-dark:#0d5fc4;
  --yellow:#f6c623;
  --gold:#d9a400;
  --mist:#d9e5ee;
  --ink:#1c1c1c;
  --body:#333;
  --white:#fff;
  --black:#000;
}
*{box-sizing:border-box;margin:0;padding:0}
html,body{width:1200px;height:4491px;overflow:hidden}
body{position:relative;font-family:"Roboto",Arial,sans-serif;color:var(--body);background:var(--white)}
.abs{position:absolute}
.head{font-family:"Roboto Condensed","Arial Narrow",sans-serif;font-weight:700}
.label{font-family:"Roboto Condensed",sans-serif;font-weight:700;font-size:16px;color:var(--gold);text-transform:uppercase}
.btn{position:absolute;display:flex;align-items:center;justify-content:center;font-family:"Roboto Condensed",sans-serif;font-weight:700;font-size:15px;border-radius:6px;text-transform:uppercase}
.btn-yellow{background:var(--yellow);color:var(--ink)}
.btn-outline{border:2px solid var(--ink);color:var(--ink)}
p{font-size:15px;line-height:25px}

/* top bar & header */
.topbar{left:375px;top:0;width:825px;height:42px;background:var(--blue);clip-path:polygon(22px 0,100% 0,100% 100%,0 100%);color:var(--white);font-size:14px;display:flex;align-items:center;gap:46px;padding-left:75px}
.brand{display:flex;align-items:center;gap:8px}
.brand-dot{width:48px;height:48px;border-radius:50%;background:var(--blue)}
.brand-name{font-family:"Roboto Condensed",sans-serif;font-weight:700;color:var(--blue);line-height:1}
.nav{left:440px;top:70px;display:flex;gap:28px;font-size:15px;color:var(--ink)}
.nav .active{color:var(--blue);text-decoration:underline}

/* hero */
.hero{left:0;top:115px;width:1200px;height:610px;background:linear-gradient(180deg,#2b3d55 0%,#5b4a3c 45%,#3a3c44 100%)}
.hero-title{width:1200px;text-align:center;color:var(--white)}

/* about */
.about-photo{left:120px;top:825px;width:438px;height:430px;border-radius:18px;background:linear-gradient(135deg,#cfd3d4,#8d8f8c 60%,#a79a8a)}
.about-title{font-size:36px;line-height:42px;color:var(--blue)}

/* mission */
.mission{left:0;top:1343px;width:1200px;height:624px;background:var(--mist)}
.card{position:absolute;top:1630px;width:312px;height:218px;background:var(--white);border-radius:12px;text-align:center;padding-top:56px}
.card h3{font-family:"Roboto Condensed",sans-serif;font-weight:700;font-size:25px;color:var(--ink);margin-bottom:10px}
.card p{padding:0 40px}
.icon{position:absolute;top:-50px;left:111px;width:90px;height:90px;border-radius:50%;background:var(--white);border:3px solid var(--blue);display:flex;align-items:center;justify-content:center}

/* stats */
.stats{left:0;top:1967px;width:1200px;height:203px;background:var(--blue);color:var(--white)}
.stat{position:absolute;top:50px;text-align:center;width:220px}
.stat b{display:block;font-family:"Roboto Condensed",sans-serif;font-size:38px;font-weight:700;line-height:44px}
.stat span{font-size:15px;line-height:24px}

/* investors */
.logo-card{position:absolute;width:230px;height:130px;border:2px solid #e2e2e2;border-radius:12px;display:flex;align-items:center;justify-content:center;gap:8px;font-family:"Roboto",sans-serif;font-weight:500;font-size:28px;color:#1d2a55}
.logo-card i{display:block;width:22px;height:22px;border-radius:50%;background:var(--blue)}

/* testimonial */
.testi{left:0;top:2720px;width:1200px;height:490px;background:var(--yellow)}
.video{left:645px;top:2786px;width:438px;height:319px;border-radius:16px;background:linear-gradient(135deg,#0c1830,#3a2a2a 55%,#c2552a)}
.play{position:absolute;left:191px;top:132px;width:58px;height:58px;border:3px solid var(--white);border-radius:50%}
.play:after{content:"";position:absolute;left:21px;top:15px;border-left:18px solid var(--white);border-top:11px solid transparent;border-bottom:11px solid transparent}

/* programs */
.tile{position:absolute;border-radius:14px;overflow:hidden;color:var(--white);font-family:"Roboto Condensed",sans-serif;font-weight:700}
.tile span{position:absolute;left:26px;bottom:22px;line-height:28px}

/* footer */
.footer{left:0;top:3990px;width:1200px;height:501px;background:var(--black);color:var(--white)}
.foot-links{left:537px;top:4145px;font-size:15px;line-height:31px;color:var(--white)}
.cta{left:720px;top:4128px;width:353px;height:242px;background:var(--yellow);border-radius:18px;padding:24px 24px}
</style>
</head>
<body>

<!-- Top bar -->
<div class="abs topbar">
  <span>
    <svg width="10" height="13" viewBox="0 0 10 13"><path d="M5 0a5 5 0 0 0-5 5c0 4 5 8 5 8s5-4 5-8a5 5 0 0 0-5-5zm0 7a2 2 0 1 1 0-4 2 2 0 0 1 0 4z" fill="#fff"/></svg>
    | 418 Tidewater Lane, Suite 210 Marlow Bay, CA 92011-4400
  </span>
  <span>
    <svg width="12" height="12" viewBox="0 0 24 24"><path d="M6.6 10.8a15 15 0 0 0 6.6 6.6l2.2-2.2c.3-.3.7-.4 1-.2 1.1.4 2.3.6 3.6.6.6 0 1 .4 1 1V20c0 .6-.4 1-1 1A17 17 0 0 1 3 4c0-.6.4-1 1-1h3.5c.6 0 1 .4 1 1 0 1.3.2 2.5.6 3.6.1.3 0 .7-.2 1z" fill="#fff"/></svg>
    | +1 555 014 2290
  </span>
</div>

<div class="abs brand" style="left:110px;top:34px">
  <div class="brand-dot"></div>
  <div>
    <div class="brand-name" style="font-size:34px">HARBORLIGHT</div>
    <div class="brand-name" style="font-size:13px;color:#555">CHAMBER OF COMMERCE</div>
  </div>
</div>

<nav class="abs nav">
  <span class="active">What We Do</span><span>Members</span><span>Programs</span><span>About</span><span>Industry Insights</span><span>News Blog</span><span>Events</span>
</nav>

<!-- Hero -->
<div class="abs hero" role="img" aria-label="Historic downtown street with church steeple, palm trees and parked cars"></div>
<div class="abs hero-title head" style="top:290px;font-size:54px;line-height:64px">WELCOME TO HARBORLIGHT</div>
<div class="abs hero-title head" style="top:355px;font-size:38px;line-height:48px;letter-spacing:1px">CHAMBER OF COMMERCE</div>
<p class="abs hero-title" style="top:418px;font-size:15px;line-height:24px">Lorem ipsum dolor sit amet, consectetur adipiscing elit, sed do eiusmod tempor<br>dolore magna aliqua.</p>
<div class="btn btn-yellow" style="left:536px;top:488px;width:128px;height:44px">Get Started</div>
<svg class="abs" style="left:0;top:670px" width="1200" height="60" viewBox="0 0 1200 60" preserveAspectRatio="none">
  <path d="M0 35 C150 -5 250 55 400 25 S650 0 800 25 S1050 55 1200 30 L1200 60 L0 60Z" fill="var(--blue)"/>
  <path d="M0 50 C150 10 250 65 400 38 S650 15 800 38 S1050 65 1200 45 L1200 60 L0 60Z" fill="#fff"/>
</svg>

<!-- About -->
<div class="abs about-photo" role="img" aria-label="Business team meeting around a conference table"></div>
<div class="abs label" style="left:630px;top:860px">About Us</div>
<h2 class="abs head about-title" style="left:630px;top:885px">HARBORLIGHT CHAMBER OF<br>COMMERCE</h2>
<p class="abs" style="left:630px;top:980px;width:460px">Lorem ipsum dolor sit amet, consectetur adipiscing elit, sed do eiusmod tempor incididunt ut labore et dolore magna aliqua. Quis ipsum suspendisse ultrices gravida. Risus commodo viverra maecenas accumsan lacus vel facilisis.</p>
<p class="abs" style="left:630px;top:1083px;width:460px">Lorem ipsum dolor sit amet, consectetur adipiscing elit, sed do eiusmod tempor incididunt ut labore et dolore magna aliqua. Quis ipsum suspendisse ultrices gravida.</p>
<div class="btn btn-yellow" style="left:631px;top:1175px;width:128px;height:46px">Read More</div>

<!-- Mission -->
<div class="abs mission"></div>
<svg class="abs" style="left:0;top:1335px" width="1200" height="50" viewBox="0 0 1200 50" preserveAspectRatio="none">
  <path d="M0 0 H1200 V20 C1100 40 1000 50 900 35 S700 10 600 25 S400 50 300 30 S100 0 0 20Z" fill="#fff"/>
</svg>
<div class="abs label" style="left:0;width:1200px;text-align:center;top:1472px">Our Mission</div>
<h2 class="abs head" style="left:0;width:1200px;text-align:center;top:1498px;font-size:38px;color:var(--blue)">YOUR BUSINESS ACCELERATOR</h2>

<div class="card" style="left:111px">
  <div class="icon"><svg width="46" height="46" viewBox="0 0 46 46" fill="none" stroke="var(--blue)" stroke-width="2"><circle cx="23" cy="12" r="5"/><circle cx="10" cy="16" r="4"/><circle cx="36" cy="16" r="4"/><rect x="12" y="24" width="22" height="6" rx="2"/><path d="M14 30v8M32 30v8M4 34c0-6 3-10 6-10M42 34c0-6-3-10-6-10"/></svg></div>
  <h3>Convene</h3>
  <p>Lorem ipsum dolor sit amet, consectetur adipiscing elit, sed do eiusmod tempor magna aliqua.</p>
</div>
<div class="card" style="left:444px">
  <div class="icon"><svg width="46" height="46" viewBox="0 0 46 46" fill="none" stroke="var(--blue)" stroke-width="2"><path d="M23 40s-12-12-12-21a12 12 0 0 1 24 0c0 9-12 21-12 21z"/><circle cx="23" cy="19" r="5"/><path d="M8 40h30"/></svg></div>
  <h3>Navigate</h3>
  <p>Lorem ipsum dolor sit amet, consectetur adipiscing elit, sed do eiusmod tempor magna aliqua.</p>
</div>
<div class="card" style="left:777px">
  <div class="icon"><svg width="46" height="46" viewBox="0 0 46 46" fill="none" stroke="var(--blue)" stroke-width="2"><path d="M6 20h8l18-10v26L14 26H6z"/><path d="M12 26l3 10h5l-3-10M36 18h5M36 13l4-3M36 23l4 3"/></svg></div>
  <h3>Advocate</h3>
  <p>Lorem ipsum dolor sit amet, consectetur adipiscing elit, sed do eiusmod tempor magna aliqua.</p>
</div>

<!-- Stats -->
<div class="abs stats">
  <div class="stat" style="left:124px"><b>114</b><span>Workplace Wellness Certified Companies</span></div>
  <div class="stat" style="left:358px"><b>1,200+</b><span>Lantern Alumni Shaping<br>HCC Future</span></div>
  <div class="stat" style="left:613px"><b>1,000+</b><span>Companies Nominated<br>Yearly For The Small Business Celebration</span></div>
  <div class="stat" style="left:862px"><b>1,800+</b><span>Professionals Connected<br>Through Networking</span></div>
</div>

<!-- Investors -->
<div class="abs label" style="left:111px;top:2250px">Investors</div>
<h2 class="abs head" style="left:111px;top:2275px;font-size:36px;color:var(--blue)">HC CHAMBER INVESTORS</h2>
<div class="logo-card" style="left:111px;top:2355px;font-size:20px"><i></i>Northmark</div>
<div class="logo-card" style="left:360px;top:2355px"><i></i>linkway</div>
<div class="logo-card" style="left:609px;top:2355px;font-size:22px"><i></i>Ledgerly</div>
<div class="logo-card" style="left:858px;top:2355px;font-size:22px"><i></i>Alderco</div>
<div class="logo-card" style="left:111px;top:2503px"><i></i>keelby</div>
<div class="logo-card" style="left:360px;top:2503px"><i></i>Glimmer</div>
<div class="logo-card" style="left:609px;top:2503px"><i></i>Aimwell</div>
<div class="logo-card" style="left:858px;top:2503px"><i></i>formcraft</div>

<!-- Testimonial -->
<div class="abs testi" role="img" aria-label="Warm yellow backdrop of a seated audience"></div>
<div class="abs label" style="left:111px;top:2805px;color:var(--ink)">Our Testimonials</div>
<h2 class="abs head" style="left:111px;top:2830px;font-size:36px;color:var(--ink)">WHY JOIN THE CHAMBER?</h2>
<p class="abs" style="left:111px;top:2885px;width:460px;color:var(--ink)">Lorem ipsum dolor sit amet, consectetur adipiscing elit, sed do eiusmod tempor incididunt ut labore et dolore magna aliqua. Quis ipsum suspendisse ultrices gravida. Risus commodo viverra maecenas accumsan lacus vel facilisis.</p>
<p class="abs" style="left:111px;top:2997px;width:460px;color:var(--ink)">– Dana Whitcombe, Chief Growth Officer,<br>Harborlight Chamber of Commerce</p>
<div class="btn btn-outline" style="left:112px;top:3063px;width:162px;height:44px;font-size:14px">Join Now</div>
<div class="abs video" role="img" aria-label="Speaker with a microphone on a stage under spotlights"><div class="play"></div></div>
<svg class="abs" style="left:0;top:3160px" width="1200" height="52" viewBox="0 0 1200 52" preserveAspectRatio="none">
  <path d="M0 30 C120 5 220 45 350 30 S560 0 700 25 S950 50 1050 28 S1160 15 1200 25 V52 H0Z" fill="#fff"/>
</svg>

<!-- Featured programs -->
<div class="abs label" style="left:0;width:1200px;text-align:center;top:3328px">Featured Event</div>
<h2 class="abs head" style="left:0;width:1200px;text-align:center;top:3353px;font-size:36px;color:var(--blue)">FEATURED PROGRAMS</h2>
<div class="tile" style="left:111px;top:3443px;width:474px;height:445px;background:linear-gradient(160deg,#b98b6a,#6d4a38 70%,#2d1f1a)" role="img" aria-label="Two women smiling over a tablet at a networking event"><span style="font-size:24px;left:47px;bottom:40px">NETWORKING &amp; EVENTS</span></div>
<div class="tile" style="left:593px;top:3443px;width:244px;height:198px;background:linear-gradient(180deg,#6f7378,#3a3a3c)" role="img" aria-label="Audience applauding at an awards ceremony"><span style="font-size:22px">Awards &amp;<br>Recognition</span></div>
<div class="tile" style="left:845px;top:3443px;width:244px;height:198px;background:linear-gradient(180deg,#7c8a6a,#3b3a30)" role="img" aria-label="Historic station building with a clock tower"><span style="font-size:19px;line-height:26px">Harbor Hall Board<br>Room Rental</span></div>
<div class="tile" style="left:593px;top:3651px;width:496px;height:237px;background:linear-gradient(160deg,#5d6f82,#3a3040 60%,#2a2428)" role="img" aria-label="Team of professionals joining hands in a huddle"><span style="font-size:19px;line-height:27px">Professional Development &amp;<br>Curriculum</span></div>

<!-- Footer -->
<div class="abs footer"></div>
<svg class="abs" style="left:0;top:3975px" width="1200" height="50" viewBox="0 0 1200 50" preserveAspectRatio="none">
  <path d="M0 0 H1200 V30 C1100 45 1000 45 880 28 S640 10 500 28 S250 48 150 32 S40 18 0 28Z" fill="var(--blue)"/>
  <path d="M0 0 H1200 V18 C1100 33 1000 33 880 16 S640 0 500 16 S250 36 150 20 S40 6 0 16Z" fill="#fff"/>
</svg>
<div class="abs brand" style="left:113px;top:4125px;gap:12px">
  <div class="brand-dot" style="width:74px;height:74px"></div>
  <div>
    <div class="brand-name" style="font-size:56px">HARBORLIGHT</div>
    <div class="brand-name" style="font-size:22px;color:#bbb">CHAMBER OF COMMERCE</div>
  </div>
</div>
<p class="abs" style="left:110px;top:4243px;color:#fff;font-size:15px;line-height:31px">Harborlight Chamber of Commerce<br>418 Tidewater Lane, Suite 210<br>Marlow Bay, CA 92011-4400<br>+1 555 014 2290</p>
<div class="abs foot-links">What We Do<br>Members<br>Programs<br>About<br>Industry Insights<br>News Blog<br>Events</div>
<div class="abs cta">
  <h3 class="head" style="font-size:23px;line-height:30px;color:var(--ink)">BECOME A HARBORLIGHT CHAMBER OF COMMERCE</h3>
  <p style="color:var(--ink);font-size:14px;line-height:23px;margin-top:6px">Lorem ipsum dolor sit amet, consectetur adipiscing elit, sed do eiusmod tempor incididunt ut labore et dolore magna aliqua.</p>
  <div class="btn btn-outline" style="left:24px;top:172px;width:162px;height:44px;font-size:14px">Become A Member</div>
</div>
<div class="abs" style="left:111px;top:4428px;width:978px;height:1px;background:#333"></div>
<div class="abs" style="left:0;width:1200px;top:4452px;text-align:center;color:#fff;font-size:14px">Copyright ©2025 Harborlight Chamber of Commerce</div>

</body>
</html>
```